Road Construction Company needs business cards

We would like a new business card designed for our business.

We're a road construction company based in Qld, Australia.

Can the business card please have the following information on it.

Name: Warren Halbeck
Position: General Manager
Phone: 0472 915 348
Email: Warren.halbeck@tovrin.com.au
Address: 87 Marrow Ave, Pendlebay, QLD, 4023
Website: www.tovrin.com.au

Visually we'd like the card to be professional and simple.

Attached is our logo.

Our website is www.tovrin.com.au

Target Market(s)

Men aged 25-60

Contact Information for Business Card

As listed in project description

Font styles to use
Serif

Requirements
Must have
• Large logo on back of card

```html
<!DOCTYPE html>
<html lang="en">
<head>
<meta charset="utf-8">
<title>Tovrin – Business Card</title>
<link rel="stylesheet" href="https://fonts.googleapis.com/css2?family=Exo+2:ital,wght@0,400;0,600;0,800;1,400&display=swap">
<style>
  :root {
    --page-bg: #2b2b2d;
    --card-bg: #1c1d20;
    --card-bg-pattern-a: #222326;
    --card-bg-pattern-b: #16171a;
    --brand-blue: #0f5fc4;
    --accent-blue: #2a86d6;
    --text-light: #f1f1f1;
    --rule: #8a8a8a;
  }
  * { box-sizing: border-box; margin: 0; padding: 0; }
  html, body {
    width: 1200px; height: 1108px; overflow: hidden;
    background: var(--page-bg);
    font-family: "Exo 2", sans-serif;
  }
  .sheet {
    position: relative; width: 1200px; height: 1108px;
  }
  .card {
    position: absolute; top: 244px;
    width: 400px; height: 620px;
    border-radius: 22px;
    background: var(--card-bg);
    overflow: hidden;
    box-shadow: 0 18px 40px rgba(0,0,0,.45);
  }
  .card--front { left: 150px; }
  .card--back { left: 650px; }

  .wordmark {
    font-family: "Exo 2", sans-serif;
    font-weight: 800;
    color: var(--brand-blue);
    letter-spacing: 2px;
    text-align: center;
    line-height: 1;
  }
  .card--front .wordmark {
    position: absolute; top: 128px; left: 0; right: 0;
    font-size: 68px;
  }

  .person {
    position: absolute; top: 300px; left: 0; right: 0; text-align: center;
  }
  .person__name {
    font-weight: 800; font-size: 26px; letter-spacing: 1px;
    text-transform: uppercase; color: var(--brand-blue);
  }
  .person__role {
    font-weight: 400; font-size: 20px; color: var(--accent-blue);
    margin-top: 2px;
  }

  .icon-row {
    position: absolute; top: 382px; left: 40px; right: 40px;
    display: flex; align-items: center; gap: 8px;
  }
  .icon-row__rule { flex: 1; height: 1px; background: var(--rule); }
  .icon-row svg { display: block; }

  .contacts {
    position: absolute; top: 428px; left: 0; right: 0;
    text-align: center; color: var(--text-light);
    font-size: 18px; line-height: 26px;
  }
  .divider {
    position: absolute; top: 516px; left: 70px; right: 70px;
    height: 1px; background: var(--rule);
  }
  .address {
    position: absolute; top: 530px; left: 0; right: 0;
    text-align: center; color: var(--text-light);
    font-size: 18px; line-height: 26px;
  }

  .back-texture {
    position: absolute; inset: 0;
    background: linear-gradient(135deg, var(--card-bg-pattern-a), var(--card-bg-pattern-b) 55%, var(--card-bg-pattern-a));
  }
  .card--back .wordmark {
    position: absolute; top: 400px; left: 0; right: 0;
    font-size: 50px;
  }
</style>
</head>
<body>
<main class="sheet">

  <section class="card card--front" aria-label="Card front">
    <div class="wordmark">TOVRIN</div>

    <div class="person">
      <div class="person__name">Warren Halbeck</div>
      <div class="person__role">General Manager</div>
    </div>

    <div class="icon-row">
      <span class="icon-row__rule"></span>
      <svg width="28" height="28" viewBox="0 0 28 28" aria-label="Phone">
        <rect width="28" height="28" rx="5" fill="var(--brand-blue)"/>
        <path d="M9 7c1 0 2 3 2 4s-1 1-1 2 3 5 5 5 1-1 2-1 4 1 4 2-2 3-3 3C11 22 6 16 6 10c0-1 2-3 3-3z" fill="none" stroke="#1c1d20" stroke-width="1.6"/>
      </svg>
      <svg width="28" height="28" viewBox="0 0 28 28" aria-label="Email">
        <rect width="28" height="28" rx="5" fill="var(--brand-blue)"/>
        <rect x="6" y="9" width="16" height="11" fill="none" stroke="#1c1d20" stroke-width="1.6"/>
        <path d="M6 9l8 6 8-6" fill="none" stroke="#1c1d20" stroke-width="1.6"/>
      </svg>
      <svg width="28" height="28" viewBox="0 0 28 28" aria-label="Website">
        <rect width="28" height="28" rx="5" fill="var(--brand-blue)"/>
        <circle cx="14" cy="14" r="7.5" fill="none" stroke="#1c1d20" stroke-width="1.6"/>
        <ellipse cx="14" cy="14" rx="3.2" ry="7.5" fill="none" stroke="#1c1d20" stroke-width="1.3"/>
        <path d="M6.5 14h15" stroke="#1c1d20" stroke-width="1.3"/>
      </svg>
      <span class="icon-row__rule"></span>
    </div>

    <div class="contacts">
      <div>0472 915 348</div>
      <div>Warren.halbeck@tovrin.com.au</div>
      <div>www.tovrin.com.au</div>
    </div>

    <div class="divider"></div>

    <div class="address">
      <div>87 Marrow Ave</div>
      <div>Pendlebay, QLD, 4023</div>
    </div>
  </section>

  <section class="card card--back" aria-label="Card back">
    <div class="back-texture" role="img" aria-label="Repeated tonal company name pattern in dark gloss"></div>
    <div class="wordmark">TOVRIN</div>
  </section>

</main>
</body>
</html>
```